menu board design: rustle burger

we are a burger restaurant.
we need to re design our menu board to fit within the new design of the restaurant. we are after something simple and easy to read. the overall look and feel of the design should be inline with the design of the shop.

Target Market(s)

18-40 male and female

Colors

Designer to choose colors to be used in the design.

Requirements
Must have
• easy to read. good layout. white background. branding included in design.

```html
<!DOCTYPE html>
<html lang="en">
<head>
<meta charset="utf-8">
<title>Rustle Burger – Menu Board</title>
<link rel="stylesheet" href="https://fonts.googleapis.com/css2?family=Bangers&family=Exo+2:wght@400;600;700&display=swap">
<style>
  :root{
    --blue:#1b4c8e;
    --gold:#d2b42b;
    --maroon:#8a1c3c;
    --ink:#1e1e1e;
    --paper:#ffffff;
    --ornament:#c9d6e8;
  }
  *{margin:0;padding:0;box-sizing:border-box}
  html,body{width:1200px;height:600px;overflow:hidden;background:var(--paper)}
  .board{position:relative;width:1200px;height:600px;font-family:"Exo 2",sans-serif;color:var(--ink)}
  .abs{position:absolute}

  .ornament{position:absolute;background:var(--ornament);border-radius:3px}
  .edge-rule{position:absolute;width:2px;background:var(--blue)}

  .banner{position:absolute;background:var(--gold);display:flex;align-items:center;justify-content:center;
    font-family:"Bangers",sans-serif;letter-spacing:1px;color:var(--blue);line-height:1}
  .banner--lg{font-size:31px}
  .banner--md{font-size:23px;color:var(--maroon)}
  .banner--step{font-family:"Exo 2",sans-serif;font-weight:700;font-size:11.5px;letter-spacing:0}

  .intro{font-size:11px;line-height:14.5px;text-align:center}
  .note{font-weight:700;color:var(--blue);font-size:11.5px;text-align:center}

  .item{position:absolute;width:315px}
  .item__row{display:flex;align-items:baseline;color:var(--gold);font-weight:600;font-size:11.5px;line-height:14px}
  .item__dots{flex:1;border-bottom:1.5px dotted var(--gold);margin:0 2px 3px}
  .item__desc{font-size:9.8px;line-height:13.2px;margin-top:2px;text-align:justify}

  .brand{position:absolute;left:467px;top:40px;width:258px;text-align:center;color:var(--blue);
    font-weight:700;font-size:52px;line-height:58px}
  .slogan{position:absolute;left:467px;top:256px;width:258px;text-align:center;color:var(--blue);
    font-size:13px;letter-spacing:5.2px}

  .divider{position:absolute;top:351px;height:0;border-top:1.5px dashed var(--blue)}

  .sides .item__row{font-size:15px;line-height:18px}
  .sides .item__dots{border-bottom-width:2px}

  .gold{color:var(--gold);font-weight:600}
  .choice{font-size:10.6px;line-height:14.4px;color:var(--gold);text-align:justify}
  .pack .item__row{font-size:11px}
  .sauce{font-weight:700;color:var(--blue);font-size:11.5px;line-height:14.5px}
  .illustration{position:absolute;border-radius:8px}
</style>
</head>
<body>
<div class="board">

  <div class="ornament" role="img" aria-label="Decorative scroll flourish" style="left:36px;top:4px;width:100px;height:22px"></div>
  <div class="ornament" role="img" aria-label="Decorative scroll flourish" style="left:4px;top:35px;width:24px;height:100px"></div>
  <div class="ornament" role="img" aria-label="Decorative scroll flourish" style="left:1064px;top:4px;width:100px;height:22px"></div>
  <div class="ornament" role="img" aria-label="Decorative scroll flourish" style="left:1172px;top:35px;width:24px;height:100px"></div>
  <div class="ornament" role="img" aria-label="Decorative scroll flourish" style="left:4px;top:465px;width:24px;height:100px"></div>
  <div class="ornament" role="img" aria-label="Decorative scroll flourish" style="left:36px;top:572px;width:100px;height:22px"></div>
  <div class="ornament" role="img" aria-label="Decorative scroll flourish" style="left:1172px;top:465px;width:24px;height:100px"></div>
  <div class="ornament" role="img" aria-label="Decorative scroll flourish" style="left:1064px;top:572px;width:100px;height:22px"></div>
  <div class="edge-rule" style="left:21px;top:141px;height:315px"></div>
  <div class="edge-rule" style="left:1177px;top:141px;height:315px"></div>

  <!-- beef burgers -->
  <div class="banner banner--lg" style="left:126px;top:35px;width:207px;height:30px">BEEF BURGERS</div>
  <p class="intro abs" style="left:69px;top:71px;width:315px">All our patties are 100% natural beef. We know because we grind it ourselves, smashed to order on a hot grill rite in from of you</p>
  <p class="note abs" style="left:69px;top:123px;width:315px">DOUBLE PATTY ADD 4</p>

  <div class="item" style="left:67px;top:141px">
    <div class="item__row"><span>CLASSIC BEEF</span><span class="item__dots"></span><span>8.9</span></div>
    <p class="item__desc">Shredded lettuce, sliced tomato, caramelised onions, beetroot and BBQ sauce on a buttered sesame seed bum.</p>
  </div>
  <div class="item" style="left:67px;top:193px">
    <div class="item__row"><span>CHEESE BURGER</span><span class="item__dots"></span><span>9.5</span></div>
    <p class="item__desc">Dill pickles, minced onion, american cheese, mustard and ketchup on soft milk bun.</p>
  </div>
  <div class="item" style="left:67px;top:240px">
    <div class="item__row"><span>FLAME GRILL</span><span class="item__dots"></span><span>9.5</span></div>
    <p class="item__desc">Shredded lettuce, sliced tomato, minced onion, dill pickles, american cheese, mayo and ketchup on a soft bun.</p>
  </div>
  <div class="item" style="left:67px;top:288px">
    <div class="item__row"><span>BIG RUS</span><span class="item__dots"></span><span>9.9</span></div>
    <p class="item__desc">Shredded lettuce, dil pickles, minced onion, american cheese and special sauce on a soft milk bun.</p>
  </div>

  <!-- brand -->
  <div class="brand">Rustle<br>Burger</div>
  <p class="slogan">GRILLED FRESH DAILY</p>

  <!-- chicken burgers -->
  <div class="banner banner--lg" style="left:816px;top:35px;width:268px;height:30px">CHICKEN BURGERS</div>
  <p class="intro abs" style="left:809px;top:70px;width:316px">All our patties are 100% natural beef. We know because we grind it ourselves, smashed to order on a hot grill rite in from of you</p>
  <p class="note abs" style="left:809px;top:122px;width:316px">DOUBLE PATTY ADD 4</p>

  <div class="item" style="left:811px;top:140px">
    <div class="item__row"><span>CLASSIC BEEF</span><span class="item__dots"></span><span>8.9</span></div>
    <p class="item__desc">Shredded lettuce, sliced tomato, caramelised onions, beetroot and BBQ sauce on a buttered sesame seed bum.</p>
  </div>
  <div class="item" style="left:811px;top:192px">
    <div class="item__row"><span>CHEESE BURGER</span><span class="item__dots"></span><span>9.5</span></div>
    <p class="item__desc">Dill pickles, minced onion, american cheese, mustard and ketchup on soft milk bun.</p>
  </div>
  <div class="item" style="left:811px;top:239px">
    <div class="item__row"><span>FLAME GRILL</span><span class="item__dots"></span><span>9.5</span></div>
    <p class="item__desc">Shredded lettuce, sliced tomato, minced onion, dill pickles, american cheese, mayo and ketchup on a soft bun.</p>
  </div>
  <div class="item" style="left:811px;top:287px">
    <div class="item__row"><span>TRUFFLED</span><span class="item__dots"></span><span>9.9</span></div>
    <p class="item__desc">Rocket, caramelised onion, dill pickles, havarti cheese and truffle infused mayo on a soft milk bun.</p>
  </div>

  <div class="divider" style="left:92px;width:376px"></div>
  <div class="divider" style="left:719px;width:361px"></div>

  <!-- sides -->
  <div class="banner banner--lg" style="left:527px;top:338px;width:135px;height:36px;font-size:34px">SIDES</div>
  <div class="sides">
    <div class="item" style="left:483px;top:395px;width:219px">
      <div class="item__row"><span>FRIES</span><span class="item__dots"></span><span>3.5</span></div>
    </div>
    <div class="item" style="left:483px;top:413px;width:219px">
      <div class="item__row"><span>KENTUCKY TENDERS</span><span class="item__dots"></span><span>6.9</span></div>
    </div>
  </div>
  <p class="abs" style="left:483px;top:445px;width:222px;font-size:10px;line-height:13px;text-align:justify">Breaded and fried chicken tenders with secret seasoning. <b>(2 PCS).</b></p>
  <div class="illustration" role="img" aria-label="Line drawing of a burger" style="left:495px;top:504px;width:106px;height:60px;background:linear-gradient(#e4ebf4,#cdd9ea)"></div>
  <div class="illustration" role="img" aria-label="Line drawing of a soft drink in a glass with ice" style="left:627px;top:480px;width:54px;height:87px;background:linear-gradient(#e4ebf4,#cdd9ea)"></div>

  <!-- nachos & loaded fries -->
  <div class="banner banner--md" style="left:117px;top:366px;width:228px;height:29px">NACHOS &amp; LOADED FRIES</div>
  <div class="banner banner--step" style="left:117px;top:423px;width:74px;height:17px">STEP ONE</div>
  <div class="banner banner--step" style="left:292px;top:423px;width:74px;height:17px">STEP TWO</div>
  <p class="note abs" style="left:85px;top:452px;width:140px">CHOOSE EITHER,</p>
  <p class="note abs" style="left:263px;top:452px;width:140px">CHOOSE ONE,</p>

  <div class="item pack" style="left:65px;top:481px;width:179px">
    <div class="item__row"><span>SEASONED FRIES</span><span class="item__dots"></span><span>9.9</span></div>
  </div>
  <p class="abs gold" style="left:65px;top:510px;font-size:11.5px">OR FRESHLY COOKED</p>
  <div class="item pack" style="left:65px;top:524px;width:179px">
    <div class="item__row"><span>CORN CHIPS</span><span class="item__dots"></span><span>11.5</span></div>
  </div>
  <p class="choice abs" style="left:252px;top:481px;width:162px"><span class="gold" style="font-size:11.5px">GUACAMOLE</span> salsa fresca, guacamole, jalapeñoz, cheese sauce and sour cream.</p>
  <p class="choice abs" style="left:252px;top:524px;width:162px"><span class="gold" style="font-size:11.5px">BEEF CHILLI</span> salsa fresca, beef chilli, jalapeños, cheese sauce and sour cream.</p>

  <!-- buffalo chicken ribs -->
  <div class="banner banner--md" style="left:832px;top:367px;width:229px;height:29px">BUFFALO CHICKEN RIBS</div>
  <p class="intro abs" style="left:782px;top:415px;width:340px;font-size:10.4px;line-height:13.5px">Buffalo style fried chicken ribs smothered in one dur mouth-watering sauce. Served with a side of ranch sauce.</p>

  <div class="item pack" style="left:792px;top:469px;width:158px">
    <div class="item__row"><span>6 PACK</span><span class="item__dots"></span><span>6.9</span></div>
  </div>
  <div class="item pack" style="left:792px;top:498px;width:158px">
    <div class="item__row"><span>12 PACK</span><span class="item__dots"></span><span>12.9</span></div>
  </div>
  <div class="item pack" style="left:792px;top:527px;width:158px">
    <div class="item__row"><span>24 PACK</span><span class="item__dots"></span><span>23.9</span></div>
  </div>
  <p class="sauce abs" style="left:986px;top:485px">CLASSIC HOT SAUCE<br>OR SMOKY BBQ</p>

</div>
</body>
</html>
```